business card - Helicopter Flight Services, Flight School, etc.

We need a business card design for a new helicopter service.

We offer Helicopter Flight Services, Aerial Filming & Photography, Flight School, and Helicopter Tours. In that order.

Summit BladeAir, Inc.
Dennis Tollerby
SummitBladeair@Kestmail.com
626-418-7352

Based at the Brenwick Airport in Van Nuys, CA. The final design should communicate integrity and safety. Pictures or logos at your discretion.

Card back side - surprise me.

```html
<!DOCTYPE html>
<html lang="en">
<head>
<meta charset="utf-8">
<title>Summit BladeAir, Inc. — Business Card</title>
<link rel="stylesheet" href="https://fonts.googleapis.com/css2?family=Open+Sans:wght@400;600;700&display=swap">
<style>
  :root {
    --stage: #e9e7e4;
    --card: #ffffff;
    --brand-blue: #0a8ef5;
    --band-blue: #0690fa;
    --swoosh-dark: #2e2e2e;
    --ink-white: #ffffff;
  }
  * { box-sizing: border-box; margin: 0; padding: 0; }
  html, body { width: 1200px; height: 900px; overflow: hidden; }
  body {
    background: var(--stage);
    font-family: "Open Sans", Arial, sans-serif;
    position: relative;
  }
  .card {
    position: absolute;
    background: var(--card);
    box-shadow: 0 6px 18px rgba(0,0,0,0.18);
    overflow: hidden;
  }
  .card--front { left: 238px; top: 62px; width: 555px; height: 342px; }
  .card--back  { left: 458px; top: 518px; width: 559px; height: 344px; }
  .card__art { position: absolute; inset: 0; width: 100%; height: 100%; }

  .brand {
    position: absolute;
    display: flex;
    align-items: center;
    gap: 12px;
    color: var(--brand-blue);
    font-weight: 400;
    font-size: 20px;
    letter-spacing: 1.5px;
    line-height: 26px;
    text-transform: uppercase;
  }
  .brand__dot {
    width: 46px; height: 46px;
    border-radius: 50%;
    background: var(--brand-blue);
    flex: none;
  }
  .card--front .brand { left: 120px; top: 62px; }
  .card--back .brand { left: 211px; top: 106px; }

  .contact-name {
    position: absolute; left: 66px; top: 286px;
    color: var(--ink-white); font-weight: 700; font-size: 17px;
  }
  .contact-list {
    position: absolute; left: 262px; top: 268px;
    list-style: none; color: var(--ink-white); font-size: 14.5px;
  }
  .contact-list li { display: flex; align-items: center; gap: 12px; height: 20px; }
  .contact-list svg { width: 10px; height: 10px; fill: var(--ink-white); }

  .services {
    position: absolute; left: 0; right: 0; top: 242px;
    text-align: center; color: var(--brand-blue);
    font-weight: 600; font-size: 15px; line-height: 25px;
  }
</style>
</head>
<body>
  <section class="card card--front" aria-label="Card front">
    <svg class="card__art" viewBox="0 0 555 342" aria-hidden="true">
      <path d="M0 145 C60 200 260 205 555 172 L555 182 C300 215 80 218 0 205 Z" fill="var(--swoosh-dark)"/>
      <path d="M0 205 C80 218 300 215 555 182 L555 342 L0 342 Z" fill="var(--ink-white)"/>
      <path d="M0 212 C90 226 310 222 555 188 L555 342 L0 342 Z" fill="var(--band-blue)"/>
    </svg>
    <div class="brand"><span class="brand__dot"></span><span>Summit<br>BladeAir<br>Inc.</span></div>
    <p class="contact-name">DENNIS TOLLERBY</p>
    <ul class="contact-list">
      <li><svg viewBox="0 0 10 10"><path d="M2 0 L4 2.5 L3 3.5 C3.8 5 5 6.2 6.5 7 L7.5 6 L10 8 L8.5 10 C4 9.5 0.5 6 0 1.5 Z"/></svg>626-418-7352</li>
      <li><svg viewBox="0 0 10 10"><path d="M0 2 H10 V8 H0 Z M0 2 L5 5.5 L10 2" /></svg>SummitBladeair@Kestmail.com</li>
    </ul>
  </section>

  <section class="card card--back" aria-label="Card back">
    <div class="brand"><span class="brand__dot"></span><span>Summit<br>BladeAir<br>Inc.</span></div>
    <p class="services">Helicopter Flight Services | Aerial Filming &amp; Photography,<br>Flight School | Helicopter Tours</p>
  </section>
</body>
</html>
```